Website Design Chair in Business Administration, especially Digital Process Networks

We, the Chair in Business Administration, especially Digital Process Networks, teach in the field of Business Informatics and Business Administration at Velmont University.
We want to setup our current website in a fresh new and clean design because the design of the old page is outdated: http://dkp.uni-velmont.example/en/
The design should be created in a way that we can integrate it into Wordpress later. Furthermore, the website should have the existing website tabs (pages). We want to add the missing subcategories in the tabs, which means that when you move the mouse over a tab, subcategories/side menus should appear.
We have the goal that the website is very clear and that the students get a direct overview especially of the lectures offered. Furthermore the website should be suitable for mobile devices.
Start page:
In general we are interested in a Tile-based Design (2 or more columns) on the start page - similar to this page: https://www.hochschule-brandor.example/. Here, the fields (Digital Process Networks (DPN) with photo, Lectures of the semester, theses, study projects, projects, current events (social media wall), jobs and internship (together), new publications) should be integrated in the form of tiles with a cover picture per field and a short description.
Furthermore, we would like to position a search bar, a social media wall especially for Instagram (replaces the field current events) and the cooperation partners perhaps as sliders with logos of the companies in the lower part of the start page (see Cooperation tab on the far right) on the start page. Footer remains the same.
Research:
Display the same content more attractively.
Learning-Platform:
Furthermore only as link.
Teaching:
In addition to the existing sub-items (Lectures of the semester, teaching-archive, learning platform, theses and book lending), the "Overview of DPN courses" and the " Open Bachelor & Master theses" should be graphically displayed.
Team:
The concept of the Teamgraph including project connections should remain. Furthermore we can imagine to list the employees with photos and short description in form of tiles (1 employee on a tile) below the graph (2 or more columns of tiles).
Publications:
Continue to display a list of publications.
Jobs and internships:
The Open Positions should be divided here into Research Associates, Student Assistants and interns, so that it becomes clearer (3 columns).
Projects:
Here we are interested a Tile-based Design (2 or more columns). We want to integrate the project fields (KORUVAN, Tidal Record Vault etc.) in the form of tiles with a title image per field and a short description.
Events and cooperations should be removed as they are sufficiently represented on the start page.
Target Market(s)
Students as well as current and future project partners
Logo Text
DPN (+ optional Chair in Digital Process Networks)
Coding
Coded - Design and coding required
Number of Pages Required
5+ page
Requirements
Must have
- See description above
Nice to have
- Perhaps a design can be created in which a direct connection to research content (AI, Deep Learning etc.) and to courses (Data Science, AI in companies etc.) can be seen.

```html
<!DOCTYPE html>
<html lang="en">
<head>
<meta charset="utf-8">
<title>DPN – Digital Process Networks</title>
<link href="https://fonts.googleapis.com/css2?family=Jost:wght@400;500&display=swap" rel="stylesheet">
<style>
:root{
  --blue:#29abe2;
  --dark:#2c2c2e;
  --text:#3a3a3a;
  --line:#e2e2e2;
  --white:#fff;
}
*{box-sizing:border-box;margin:0;padding:0}
html,body{width:1200px;height:4505px;overflow:hidden;background:var(--white)}
body{font-family:'Jost',sans-serif;color:var(--text);position:relative}
.abs{position:absolute}
a{color:inherit;text-decoration:none}

.site-header{left:0;top:0;width:1200px;height:84px;background:var(--white)}
.logo{left:143px;top:16px;font-size:44px;font-weight:400;color:#1d1d1d;letter-spacing:1px;line-height:50px}
.main-nav{left:252px;top:34px;display:flex;gap:34px;font-size:10.5px;letter-spacing:.3px;text-transform:uppercase;color:#444}
.main-nav .active{color:var(--blue)}

.hero{left:0;top:84px;width:1200px;height:582px;background:linear-gradient(100deg,#cfd6da 0%,#a8b1b6 35%,#6e7478 65%,#9aa3a8 100%)}
.hero-title{left:143px;top:178px;font-size:38px;line-height:50px;color:#1e1e1e;font-weight:400;letter-spacing:.5px}
.hero-arrow{width:40px;height:40px;border-radius:50%;background:#2a2a2a;top:330px}

.section-title{width:1200px;left:0;text-align:center;font-size:38px;color:var(--blue);font-weight:500;letter-spacing:.5px}

.welcome-title{left:143px;top:755px;font-size:38px;color:var(--blue);font-weight:500}
.welcome-text{left:143px;top:822px;width:500px;font-size:13.6px;line-height:30.5px;color:#444}
.photo{background:linear-gradient(135deg,#59646c,#a8b2b8 50%,#4a535a)}

.band{left:0;width:1200px}
.band-bg{background:linear-gradient(120deg,#3a3a3c,#555558 45%,#2f2f31)}

.tile{background:var(--white);width:297px;height:160px;text-align:center}
.tile svg{margin-top:22px}
.tile-label{font-size:18px;color:#222;margin-top:10px}

.pill{background:var(--white);border:1px solid var(--line);box-shadow:0 2px 4px rgba(0,0,0,.12);height:48px;display:flex;align-items:center;justify-content:center;font-size:16px;color:#333;white-space:nowrap}

.card{background:var(--white);width:297px;height:464px}
.card-head{font-size:22px;color:var(--blue);padding:20px 12px;border-bottom:1px solid var(--line);height:72px}
.card-item{padding:14px 12px;border-bottom:1px solid var(--line);font-size:13.5px;line-height:21px;color:#444}
.card-item small{display:block;font-size:10px;line-height:18px;color:#555}
.date{font-size:10px;color:#666}
.view-all{left:12px;bottom:30px;display:flex;align-items:center;gap:8px;font-size:14px;color:#333}
.dot-icon{width:20px;height:20px;border-radius:50%;background:#222;display:inline-block;position:relative}
.dot-icon:after{content:"";position:absolute;left:7px;top:5px;border-left:7px solid #fff;border-top:5px solid transparent;border-bottom:5px solid transparent}
.pdf{font-size:11px;color:#555;margin-top:6px}

.study{background:var(--white);width:297px;height:175px;padding:14px 12px}
.study h3{font-size:19px;font-weight:400;color:#222;margin-top:8px}
.study p{font-size:9.5px;color:#555;margin-top:8px;line-height:15px}
.study .levels{font-size:12px;color:var(--blue);margin-top:2px}

.post-text{left:150px;top:3905px;width:900px;text-align:center;font-size:19.5px;line-height:32px;color:#444}
.post-text a{color:var(--blue);text-decoration:underline}

.footer-title{font-size:24px;color:#fff;font-weight:400}
.footer-links{font-size:11px;color:#ddd;line-height:24px}
.social{width:48px;height:48px;border:2px solid #777;border-radius:50%}
.social:after{content:"";position:absolute;left:18px;top:18px;width:8px;height:8px;border-radius:50%;background:#999}
</style>
</head>
<body>

<header class="abs site-header">
  <div class="abs logo">DPN</div>
  <nav class="abs main-nav">
    <a class="active">Research</a><a>Learning-Platform</a><a>Teaching</a><a>Team</a><a>Publications</a><a>Jobs</a><a>Projects</a><a>Events</a><a>Cooperations</a>
  </nav>
</header>

<section>
  <div class="abs hero" role="img" aria-label="Photo of students and a lecturer discussing work at a laptop"></div>
  <h1 class="abs hero-title">DIGITAL PROCESS<br>NETWORKS</h1>
  <div class="abs hero-arrow" style="left:55px"><svg width="40" height="40"><path d="M23 13l-7 7 7 7" stroke="#fff" stroke-width="3" fill="none"/></svg></div>
  <div class="abs hero-arrow" style="left:1103px"><svg width="40" height="40"><path d="M17 13l7 7-7 7" stroke="#fff" stroke-width="3" fill="none"/></svg></div>
  <svg class="abs" style="left:0;top:600px" width="1200" height="70" viewBox="0 0 1200 70" preserveAspectRatio="none">
    <polygon points="0,20 1100,62 1200,58 1200,70 0,70" fill="var(--blue)"/>
    <polygon points="0,16 0,70 1200,70 1200,66 1102,60" fill="#fff"/>
  </svg>
</section>

<section>
  <h2 class="abs welcome-title">WELCOME TO DPN</h2>
  <p class="abs welcome-text">The Chair in Business Administration, especially Digital Process Networks at Velmont University, studies how data-driven services are designed, run and managed in fields such as health and logistics. Led by Prof. Dr.-Ing. Henrik Vessel, the team explores how experimental design methods, together with distributed and analytic approaches, produce adaptive services and new solutions. This work takes place in basic and applied projects carried out with research and industry partners. Results are tested and refined in industry projects by the Adaptive Systems Lab (ASL) at the Northern Institute for Applied Intelligence (NIAI).</p>
  <div class="abs photo" style="left:700px;top:766px;width:356px;height:241px" role="img" aria-label="Group photo of the chair team"></div>
  <div class="abs photo" style="left:700px;top:1012px;width:188px;height:109px" role="img" aria-label="Photo of a lecture hall"></div>
  <div class="abs photo" style="left:893px;top:1012px;width:163px;height:109px" role="img" aria-label="Photo of a seminar room"></div>
</section>

<section>
  <div class="abs band band-bg" style="top:1203px;height:790px;clip-path:polygon(0 0,100% 6%,100% 89%,0 96%)" role="img" aria-label="Dimmed photo of students working"></div>
  <svg class="abs" style="left:0;top:1900px" width="1200" height="90" viewBox="0 0 1200 90"><polygon points="95,56 1200,3 1200,14 140,90" fill="var(--blue)"/></svg>

  <div class="abs tile" style="left:143px;top:1331px"><svg width="64" height="64" viewBox="0 0 64 64" fill="none" stroke="var(--blue)" stroke-width="2"><rect x="12" y="8" width="38" height="50"/><rect x="18" y="4" width="38" height="50"/><circle cx="37" cy="27" r="9"/><path d="M37 18v9h9"/><path d="M24 44h26M24 49h20"/></svg><div class="tile-label">Research</div></div>
  <div class="abs tile" style="left:451px;top:1331px"><svg width="64" height="64" viewBox="0 0 64 64" fill="none" stroke="var(--blue)" stroke-width="2"><rect x="10" y="10" width="44" height="32"/><path d="M4 48h56l-4 6H8z"/></svg><div class="tile-label">Learning-Platform</div></div>
  <div class="abs tile" style="left:757px;top:1331px"><svg width="64" height="64" viewBox="0 0 64 64" fill="none" stroke="var(--blue)" stroke-width="2"><rect x="8" y="8" width="38" height="28"/><path d="M14 30l8-10 6 6 10-12M27 36v20M18 56l9-20 9 20"/><circle cx="52" cy="22" r="4"/><path d="M52 26v28M46 36h12"/></svg><div class="tile-label">Teaching</div></div>

  <div class="abs tile" style="left:143px;top:1499px"><svg width="64" height="64" viewBox="0 0 64 64" fill="none" stroke="var(--blue)" stroke-width="2"><circle cx="32" cy="20" r="8"/><path d="M18 54v-12a14 10 0 0 1 28 0v12"/><circle cx="12" cy="28" r="6"/><circle cx="52" cy="28" r="6"/><path d="M2 54v-10a10 8 0 0 1 14-6M62 54v-10a10 8 0 0 0-14-6"/></svg><div class="tile-label">Team</div></div>
  <div class="abs tile" style="left:451px;top:1499px"><svg width="64" height="64" viewBox="0 0 64 64" fill="none" stroke="var(--blue)" stroke-width="2"><rect x="10" y="6" width="46" height="52"/><path d="M4 14v40a4 4 0 0 0 6 4"/><rect x="24" y="10" width="28" height="10"/><rect x="16" y="26" width="14" height="12"/><path d="M34 28h18M34 34h18M16 44h36M16 50h36"/></svg><div class="tile-label">Publications</div></div>
  <div class="abs tile" style="left:757px;top:1499px"><svg width="64" height="64" viewBox="0 0 64 64" fill="none" stroke="var(--blue)" stroke-width="2"><circle cx="28" cy="24" r="11"/><path d="M10 56a18 14 0 0 1 36 0"/><circle cx="46" cy="14" r="7"/><path d="M51 19l7 7"/></svg><div class="tile-label">Jobs</div></div>

  <div class="abs tile" style="left:143px;top:1669px"><svg width="64" height="64" viewBox="0 0 64 64" fill="none" stroke="var(--blue)" stroke-width="2"><rect x="22" y="4" width="20" height="14"/><path d="M32 18v10M12 28h40M12 28v8M32 28v8M52 28v8"/><rect x="4" y="36" width="16" height="20"/><rect x="24" y="36" width="16" height="20"/><rect x="44" y="36" width="16" height="20"/></svg><div class="tile-label">Projects</div></div>
  <div class="abs tile" style="left:451px;top:1669px"><svg width="64" height="64" viewBox="0 0 64 64" fill="none" stroke="var(--blue)" stroke-width="2"><rect x="6" y="10" width="52" height="48"/><path d="M6 20h52M20 4v10M44 4v10"/><text x="32" y="50" text-anchor="middle" font-family="Jost,sans-serif" font-size="24" fill="var(--blue)" stroke="none">19</text></svg><div class="tile-label">Events</div></div>
  <div class="abs tile" style="left:757px;top:1669px"><svg width="64" height="64" viewBox="0 0 64 64" fill="none" stroke="var(--blue)" stroke-width="2"><circle cx="24" cy="32" r="14"/><circle cx="40" cy="32" r="14"/><path d="M32 4v8M32 52v8"/></svg><div class="tile-label">Cooperations</div></div>
</section>

<section>
  <h2 class="abs section-title" style="top:2053px">LECTURES OF THE SEMESTER</h2>
  <div class="abs pill" style="left:143px;top:2116px;width:297px">Service Management</div>
  <div class="abs pill" style="left:451px;top:2116px;width:297px">KI in Unternehmen</div>
  <div class="abs pill" style="left:757px;top:2116px;width:297px">Service Engineering</div>
  <div class="abs pill" style="left:350px;top:2181px;width:500px">Seminar "Datenplattformen und vernetzte Dienste"</div>
</section>

<section>
  <div class="abs band band-bg" style="top:2326px;height:700px;clip-path:polygon(0 5%,100% 0,100% 99%,0 92%)" role="img" aria-label="Dimmed photo of an office workspace"></div>
  <svg class="abs" style="left:0;top:2970px" width="1200" height="80" viewBox="0 0 1200 80"><polygon points="0,0 1200,50 1200,56 1055,75 1040,72 0,8" fill="var(--blue)"/></svg>

  <div class="abs card" style="left:143px;top:2436px">
    <div class="card-head">Jobs</div>
    <div class="card-item" style="height:104px">NIAI: Research Assistant with a degree in computer science to support the Project Lumen wanted!</div>
    <div class="card-item" style="height:104px">VeU: Research Assistant to support Project Management wanted!</div>
    <div class="card-item" style="border:0">VeU: Research Assistant wanted!</div>
    <div class="abs view-all"><span class="dot-icon"></span>VIEW ALL</div>
  </div>

  <div class="abs card" style="left:451px;top:2436px">
    <div class="card-head">Current events</div>
    <div class="card-item" style="height:168px">Master Defense Talk<div class="date">22.10.2010</div><small>Lena Kortmann, research assistant at the chair, gave a presentation of her master thesis to Professor Vessel and other members of the chair last Thursday. The topic is "Pricing Models for Shared Sensor Records".</small></div>
    <div class="card-item" style="border:0">Press release on the launch of research project VALMIRA<div class="date">14.05.2020</div><div style="font-size:20px;color:#222;margin-top:6px;letter-spacing:1px">VALMIRA</div></div>
    <div class="abs view-all"><span class="dot-icon"></span>VIEW ALL</div>
  </div>

  <div class="abs card" style="left:757px;top:2436px">
    <div class="card-head">New publications</div>
    <div class="card-item" style="height:168px"><small>Adler, N., &amp; Vessel, H.</small><small>Context-Aware Shop Assistance Using Wearable Signals. Proceedings of the 12th Nordic Symposium on Service Design, 2020.</small><div class="pdf">▢ PDF (3.26 MB)</div></div>
    <div class="card-item" style="border:0"><small>Adler, N., &amp; Vessel, H.</small><small>Remote Coaching Platform for Youth Fitness in Small Towns. MobiCon '20 Workshop: Lessons from Mobile Care Pilots</small><div class="pdf">▢ PDF (3.26 MB)</div></div>
    <div class="abs view-all"><span class="dot-icon"></span>VIEW ALL</div>
  </div>
</section>

<section>
  <h2 class="abs section-title" style="top:3118px">PROJECTS</h2>
  <div class="abs pill" style="left:143px;top:3183px;width:97px">KORUVAN</div>
  <div class="abs pill" style="left:246px;top:3183px;width:174px">Tidal Record Vault</div>
  <div class="abs pill" style="left:426px;top:3183px;width:113px">PRAVOSYS</div>
  <div class="abs pill" style="left:545px;top:3183px;width:190px">Field Sensing Hub</div>
  <div class="abs pill" style="left:741px;top:3183px;width:100px">VALMIRA</div>
  <div class="abs pill" style="left:847px;top:3183px;width:102px">TERANOVA</div>
  <div class="abs pill" style="left:955px;top:3183px;width:100px">View All</div>
</section>

<section>
  <div class="abs band band-bg" style="top:3314px;height:450px;clip-path:polygon(0 0,100% 10%,100% 84%,0 100%)" role="img" aria-label="Dimmed photo of students studying"></div>
  <svg class="abs" style="left:0;top:3680px" width="1200" height="90" viewBox="0 0 1200 90"><polygon points="95,64 1200,0 1200,12 140,90" fill="var(--blue)"/></svg>

  <div class="abs study" style="left:143px;top:3445px">
    <svg width="52" height="62" viewBox="0 0 52 62" fill="none" stroke="#222" stroke-width="2"><path d="M6 10l20-8 20 8-20 8z"/><path d="M14 14v8a12 10 0 0 0 24 0v-8"/><path d="M6 60v-10a20 12 0 0 1 40 0v10"/></svg>
    <h3>Internship</h3><p>Gain practical experience in an internship with us – become a member of the team!</p>
  </div>
  <div class="abs study" style="left:451px;top:3445px">
    <svg width="62" height="62" viewBox="0 0 62 62" fill="none" stroke="#222" stroke-width="2"><rect x="6" y="26" width="34" height="14" rx="7" transform="rotate(-45 23 33)"/><rect x="22" y="22" width="34" height="14" rx="7" transform="rotate(-45 39 29)"/></svg>
    <h3>Theses</h3><p style="margin-top:6px">Open theses in WS 20/21</p><div class="levels">1 - Bachelor &nbsp;&nbsp;|&nbsp;&nbsp; 5 - Master</div>
  </div>
  <div class="abs study" style="left:757px;top:3445px">
    <svg width="66" height="62" viewBox="0 0 66 62" fill="none" stroke="#222" stroke-width="2"><path d="M4 10h26v46H4zM36 10h26v46H36z"/><path d="M30 8l6-4M10 20h14M10 28h14M10 36h14M42 20h14M42 28h14M42 36h14"/></svg>
    <h3>Study projects</h3><p>Get insights into exciting study projects</p>
  </div>
</section>

<section>
  <h2 class="abs section-title" style="top:3832px">POSTS</h2>
  <p class="abs post-text">Fusce vitae lectus sit amet mi pulvinar maximus. Aenean placerat, nibh vel accumsan aliquet, magna nibh <a>accumsan nibh ac tempus nunc ipsum ac tellus</a>. Cras augue magna, placerat eget nulla non, congue suscipit neque tellus venenatis.</p>
  <div class="abs" style="left:589px;top:4012px;width:22px;height:22px;border-radius:50%;background:var(--blue)"></div>
  <div class="abs" style="left:0;top:4046px;width:1200px;text-align:center;font-size:12px;color:#444">28.10.2020</div>
</section>

<footer>
  <svg class="abs" style="left:0;top:4125px" width="1200" height="380" viewBox="0 0 1200 380" preserveAspectRatio="none">
    <polygon points="0,72 1100,0 1200,26 1200,380 0,380" fill="var(--blue)"/>
    <polygon points="0,76 1200,26 1200,380 0,380" fill="var(--dark)"/>
  </svg>
  <div class="abs footer-title" style="left:143px;top:4232px">Links</div>
  <div class="abs footer-links" style="left:143px;top:4275px">Research<br>Learning-Platform<br>Teaching<br>Team<br>Publications</div>
  <div class="abs footer-links" style="left:264px;top:4275px">Jobs<br>Projects<br>Events<br>Cooperations</div>

  <div class="abs footer-title" style="left:437px;top:4232px">Newsletter Signup</div>
  <div class="abs" style="left:439px;top:4280px;font-size:10px;color:#ccc">Phasellus condimentum vitae faucibus sollicitudin metus</div>
  <div class="abs" style="left:439px;top:4304px;width:295px;height:44px;border:1px solid #666;display:flex;align-items:center;justify-content:space-between;padding:0 14px 0 18px;font-size:10px;color:#aaa">Email Address
    <svg width="30" height="22" viewBox="0 0 30 22"><rect width="30" height="22" rx="2" fill="#ccc"/><path d="M1 2l14 11 14-11" stroke="var(--dark)" stroke-width="2" fill="none"/></svg></div>

  <div class="abs footer-title" style="left:837px;top:4232px">Follow us on</div>
  <div class="abs social" style="left:839px;top:4280px" aria-label="Social network one"></div>
  <div class="abs social" style="left:895px;top:4280px" aria-label="Social network two"></div>
  <div class="abs social" style="left:951px;top:4280px" aria-label="Video channel"></div>
  <div class="abs social" style="left:1007px;top:4280px" aria-label="News feed"></div>

  <div class="abs" style="left:143px;top:4444px;width:913px;height:1px;background:#555"></div>
  <div class="abs" style="left:0;top:4462px;width:1200px;text-align:center;font-size:10px;color:#ccc">Copyright © 2020 &nbsp; Digital Process Networks. &nbsp; All rights reserved.</div>
</footer>

</body>
</html>
```